Bring me business with this creative business card

Design my new business card. I am looking for something different with an impact. People will take a look at this card & they will 1- see how different & creative I am, 2-understand what I do 3- Call me to meet me!

I make videos with a message, testimonials. I am dynamic, fun, creative & human. My new website is in construction but in the meantime you can check this old one: brightpath.ca & another one Tidebloom.com & tidebloom facebook page.
I make videos. sometimes with a cameraman, sometimes with my phone. As an ex Public Relations agent, the message is the most important thing for me. I want to make my clients shine! When they start with me they often remind me of a lamb, when I finish coaching them they are powerful like LIONS! That's why I need a powerful business card!

Target Market(s)

Entrepreneurs, solo entrepreneurs, small & medium companies & start ups. People i will meet while networking. People that need videos on their website & social Networks to get attention, to be visible. men & women. From 35 to 49 years old.
I am an ex Public relations agent. I used to send clients in traditional medias, now with videos they have more chances to be seen on google the new media. I do videos of the president, his team, his loyal clients saying how great the company is & expert videos like series so people can be seen for example every 1 st of every month with a short 2 minute video. Also with my 20 years in marketing & communications I can coach & give tips to anybody who needs it.
Target: anybody who would like my old website brightpath.ca & I also have another website but it will be off line soon: tidebloom.com could give you ideas.

Industry/Entity Type

Communications

Contact Information for Business Card

I am in Montreal,So the business cards have to be the usual size like we have in Montreal: 9 cm x 5 cm
Details:My text: Mathilde Tessier Communication Coach/Lead Voice. "MAKING YOUR BRAND SHINE ON CAMERA" off: 514-555-0147 cell: 514-555-0183. tidebloom.com
mathilde@tidebloom.com logo facebook, youtube, instagram

Colors
f37122

Requirements
Must have
• Dynamic, happy. Orange. Be creative in the look but NOT the shape of the card. Easy to read. Big enough to read.
Should not have
• No funny shapes: no round, no square, just the usual. I love creative but NOT on shape.

```html
<!DOCTYPE html>
<html lang="en">
<head>
<meta charset="utf-8">
<title>Tidebloom business card</title>
<link rel="stylesheet" href="https://fonts.googleapis.com/css2?family=Cinzel:wght@500;700&family=Lato:wght@400&family=Tinos:wght@400;700&display=swap">
<style>
  :root {
    --orange: #f05f22;
    --orange-brand: #ef6a24;
    --amber: #fba313;
    --gold: #f5a21a;
    --white: #ffffff;
    --backdrop: #ecebe8;
  }
  * { margin: 0; padding: 0; box-sizing: border-box; }
  html, body { width: 1200px; height: 900px; overflow: hidden; }
  body { background: var(--backdrop); position: relative; font-family: "Lato", sans-serif; }

  .card { position: absolute; background: var(--white); overflow: hidden; box-shadow: 0 4px 14px rgba(0,0,0,.12); }
  .card--front { left: 78px; top: 33px; width: 588px; height: 365px; }
  .card--back { left: 388px; top: 505px; width: 567px; height: 352px; }

  .card__bands { position: absolute; inset: 0; }

  .brand-mark { position: absolute; border-radius: 50%; background: linear-gradient(160deg, var(--amber), var(--orange)); }
  .card--front .brand-mark { left: 124px; top: 40px; width: 104px; height: 104px; }
  .card--back .brand-mark { left: 228px; top: 68px; width: 110px; height: 110px; }

  .brand-name { position: absolute; font-family: "Cinzel", serif; font-weight: 700; color: var(--orange-brand); white-space: nowrap; }
  .card--front .brand-name { left: 244px; top: 84px; font-size: 34px; letter-spacing: .5px; }
  .card--back .brand-name { left: 0; right: 0; top: 212px; text-align: center; font-size: 36px; letter-spacing: 2px; }

  .tagline { position: absolute; display: flex; align-items: center; gap: 8px; color: var(--gold); white-space: nowrap; }
  .tagline::before, .tagline::after { content: ""; width: 26px; height: 1.5px; background: var(--gold); }
  .card--front .tagline { left: 250px; top: 123px; font-family: "Lato", sans-serif; font-size: 15px; }
  .card--back .tagline { left: 0; right: 0; top: 255px; justify-content: center; font-family: "Tinos", serif; font-size: 16px; }

  .motto { position: absolute; left: 0; right: 0; top: 290px; text-align: center; font-family: "Tinos", serif; font-size: 18px; color: var(--orange); }

  .contact-list { position: absolute; left: 30px; top: 255px; list-style: none; color: var(--white); font-size: 15.5px; line-height: 21.5px; }
  .contact-list li { display: flex; align-items: center; gap: 9px; }
  .contact-list svg { width: 12px; height: 12px; fill: var(--white); flex: none; }

  .holder { position: absolute; right: 36px; top: 287px; text-align: right; color: var(--white); }
  .holder__name { font-family: "Tinos", serif; font-weight: 700; font-size: 23px; letter-spacing: .5px; }
  .holder__title { font-size: 15.5px; margin-top: 2px; }
</style>
</head>
<body>

<section class="card card--front">
  <svg class="card__bands" viewBox="0 0 588 365" aria-hidden="true">
    <polygon points="0,200 402,200 378,224 0,224" fill="var(--amber)"/>
    <polygon points="414,192 588,192 588,365 0,365 0,228 382,228" fill="var(--orange)"/>
  </svg>
  <div class="brand-mark" aria-hidden="true"></div>
  <div class="brand-name">TIDEBLOOM</div>
  <div class="tagline">ONE STORY ONE VOICE</div>

  <ul class="contact-list">
    <li><svg viewBox="0 0 12 12"><path d="M1 4c0-2 2-3 5-3s5 1 5 3H8V3H4v1zM2 5h8l1 6H1z"/></svg>514-555-0147</li>
    <li><svg viewBox="0 0 12 12"><path d="M3 0h6v12H3zM4 1.5v8h4v-8z"/></svg>514-555-0183</li>
    <li><svg viewBox="0 0 12 12"><path d="M0 2h12v8H0zM1 3l5 3.5L11 3v-.1H1z" fill-rule="evenodd"/></svg>mathilde@tidebloom.com</li>
    <li><svg viewBox="0 0 12 12"><circle cx="6" cy="6" r="5.5"/></svg>www.tidebloom.com</li>
  </ul>

  <div class="holder">
    <div class="holder__name">MATHILDE T</div>
    <div class="holder__title">Communication Coach/Lead Voice</div>
  </div>
</section>

<section class="card card--back">
  <div class="brand-mark" aria-hidden="true"></div>
  <div class="brand-name">TIDEBLOOM</div>
  <div class="tagline">ONE STORY ONE VOICE</div>
  <p class="motto">MAKING YOUR BRAND SHINE ON CAMERA</p>
</section>

</body>
</html>
```